Weekly Newsletter template for our niche within the Telecom Industry

We need a 'skeleton' format where we can insert our weekly information and ads.
We will do all the content in-house.
Content in both info and ads must be able to contain hyperlinks.
Our company website is: www. halvorsen-quibb.com
We think we would like something similar to the top format but with the single bar on the right side as a place to insert ads
Thank you.

```html
<!DOCTYPE html>
<html lang="en">
<head>
<meta charset="utf-8">
<title>Halvorsen Quibb – Weekly Newsletter</title>
<link rel="stylesheet" href="https://fonts.googleapis.com/css2?family=Montserrat:wght@500;600;700&family=Lato:wght@400;700&display=swap">
<style>
  :root{
    --ink:#111111;
    --body:#222222;
    --paper:#ffffff;
    --rule:#e2e2e2;
    --teal:#1aa5c0;
    --teal-text:#2aa3a8;
    --olive:#c6c84a;
    --lime-title:#c9c63c;
    --footer:#000000;
    --link-grey:#666666;
  }
  *{box-sizing:border-box;margin:0;padding:0}
  html,body{width:817px;height:1200px;overflow:hidden;background:var(--paper)}
  body{position:relative;font-family:"Lato",Arial,sans-serif;color:var(--body)}
  a{color:inherit}

  .brand{position:absolute;left:40px;top:48px;width:440px;display:flex;align-items:center;gap:16px}
  .brand-dot{flex:none;width:44px;height:44px;border-radius:50%;background:linear-gradient(135deg,var(--teal),var(--olive))}
  .brand-name{font-family:"Montserrat",Arial,sans-serif;font-weight:500;font-size:32px;letter-spacing:.5px;color:var(--ink);line-height:1;white-space:nowrap}

  .header-contact{position:absolute;left:506px;top:0;width:270px;height:162px;border-left:1px solid var(--rule);border-right:1px solid var(--rule)}
  .header-contact .icon{position:absolute;left:26px;top:60px}
  .header-contact .label{position:absolute;left:78px;top:60px;font-family:"Montserrat",Arial,sans-serif;font-weight:600;font-size:13px;color:var(--ink)}
  .header-contact .phone{position:absolute;left:78px;top:78px;font-family:"Montserrat",Arial,sans-serif;font-weight:700;font-size:19px;color:var(--ink)}

  .hero{position:absolute;left:41px;top:162px;width:453px;height:489px;background:radial-gradient(ellipse at 60% 35%,#5a7fd6 0%,#243a8a 30%,#0b1436 65%,#05070f 100%)}
  .hero-visual{position:absolute;inset:0;background:radial-gradient(ellipse at 45% 40%,rgba(240,150,200,.45) 0%,rgba(240,150,200,0) 40%),radial-gradient(ellipse at 55% 72%,rgba(80,200,255,.45) 0%,rgba(80,200,255,0) 40%)}
  .hero-caption{position:absolute;left:0;right:0;bottom:0;height:100px;background:linear-gradient(to bottom,rgba(0,0,0,0),rgba(0,0,0,.85) 35%,#000)}
  .hero-title{position:absolute;left:25px;top:406px;font-family:"Montserrat",Arial,sans-serif;font-weight:700;font-size:22.5px;color:var(--lime-title)}
  .hero-sub{position:absolute;left:25px;top:448px;font-size:17px;color:#fff;letter-spacing:-.2px}

  .lead{position:absolute;left:40px;top:676px;width:445px;font-family:"Montserrat",Arial,sans-serif;font-weight:700;font-size:17.4px;line-height:32.5px;color:var(--ink)}
  .copy{position:absolute;left:40px;top:818px;width:448px;font-size:15.6px;line-height:26.8px;color:var(--body)}
  .copy .highlight{color:var(--teal-text);font-weight:700}
  .copy p + p{margin-top:26.8px}

  .sidebar{position:absolute;left:506px;top:162px;width:270px;height:735px;background:linear-gradient(to bottom,var(--teal) 0%,#5db7a0 45%,var(--olive) 100%);color:#fff;padding:0 14px 0 12px}
  .sidebar h2{font-family:"Montserrat",Arial,sans-serif;font-weight:700;font-size:19.5px;margin-top:18px;margin-left:1px}
  .sidebar .title-rule{position:relative;margin-left:-12px;margin-top:12px;width:112px;height:2px;background:#fff}
  .sidebar .title-rule::after{content:"";position:absolute;right:-5px;top:-4px;width:10px;height:10px;border-radius:50%;background:#fff}
  .sidebar .intro{font-size:16px;line-height:27.5px;margin-top:17px}
  .date{display:inline-block;border:1px solid #fff;font-size:9px;font-weight:700;padding:1px 5px;margin-left:10px;vertical-align:middle;line-height:12px}
  .news-item p{font-size:12.8px;line-height:23.5px;margin-top:4px}
  .news-item + .news-item{border-top:1px solid rgba(255,255,255,.5);margin-top:20px;padding-top:14px}
  .news-item h3{font-weight:400;font-size:16px;line-height:27px}
  .sources{background:#fff;margin:10px -7px 0 -5px;padding:6px 8px;font-size:12.8px;line-height:24.5px;color:var(--link-grey);height:133px;overflow:hidden}
  .sources a{display:block;text-decoration:underline;white-space:nowrap}
  .view-more{display:inline-block;margin-top:16px;font-family:"Montserrat",Arial,sans-serif;font-weight:600;font-size:15px;color:#fff;text-decoration:underline}

  .ad{position:absolute;left:506px;top:907px;width:270px;height:188px;background:linear-gradient(160deg,#4a6a7a 0%,#9fb6c2 45%,#2f8fa0 100%);overflow:hidden}
  .ad-visual{position:absolute;inset:0}
  .ad-caption{position:absolute;left:0;right:0;bottom:0;height:68px;background:linear-gradient(to bottom,rgba(30,160,175,.3),#2aa1ad 40%);display:flex;align-items:flex-end;justify-content:center;padding-bottom:10px;text-align:center;font-family:"Montserrat",Arial,sans-serif;font-weight:700;font-size:13.5px;line-height:23px;color:#fff}

  .footer{position:absolute;left:0;top:1146px;width:817px;height:54px;background:var(--footer);color:#fff;font-size:16px}
  .footer .legal{position:absolute;left:0;right:0;top:16px;text-align:center}
  .footer .code{position:absolute;right:16px;top:17px}
</style>
</head>
<body>
  <div class="brand">
    <span class="brand-dot"></span>
    <span class="brand-name">HALVORSEN QUIBB</span>
  </div>

  <div class="header-contact">
    <svg class="icon" width="42" height="42" viewBox="0 0 42 42" aria-hidden="true">
      <defs><linearGradient id="callGrad" x1="0" y1="0" x2="1" y2="1"><stop offset="0" stop-color="#1aa5c0"/><stop offset="1" stop-color="#c6c84a"/></linearGradient></defs>
      <circle cx="21" cy="21" r="20" fill="url(#callGrad)"/>
      <path d="M14 12c1-1 2.5-1 3.2.2l1.6 2.8c.5.9.2 1.9-.6 2.5l-1.2.9c1 2.3 2.8 4.2 5.1 5.2l.9-1.2c.6-.8 1.7-1 2.5-.5l2.8 1.6c1.1.7 1.2 2.2.2 3.1l-1.3 1.2c-1.3 1.2-3.3 1.4-4.9.6-4.5-2.2-8-5.7-10.2-10.2-.8-1.6-.5-3.5.7-4.8z" fill="#fff"/>
      <path d="M23 11a8 8 0 0 1 8 8M23 15a4 4 0 0 1 4 4" stroke="#fff" stroke-width="1.8" fill="none" stroke-linecap="round"/>
    </svg>
    <div class="label">CALL US NOW:</div>
    <div class="phone">+1 555 010 0142</div>
  </div>

  <section class="hero">
    <div class="hero-visual" role="img" aria-label="Photo of a glowing robotic hand touching a digital circuit surface"></div>
    <div class="hero-caption"></div>
    <div class="hero-title">AL-DRIVEN TELECOM SECURITY</div>
    <div class="hero-sub">Smart Protection with Machine Learning</div>
  </section>

  <h1 class="lead">Using highly developed artificial intelligence, machine learning, telecom analytics, database manipulation, and human oversight --we can tell you what is actually on your network.</h1>

  <div class="copy">
    <p><span class="highlight">Send 1% of your traffic, randomly, throughout the day,</span><br>and we'll tell you what is really on your network. End Tracebacks, huge fines, and inquiries from the FCC and multiple states' AG.</p>
    <p>With the guidance of some of the best telecommunications attorneys in the nation, we keep this process legal meeting Federal privacy and wiretap regulations.WIth Nimbus's best partners on the Nimbus Cloud, we've developed monitoring that will find virtually all of fraud on your network, blatant TCPA and TSR violations.This is the best in the business, by far.</p>
  </div>

  <aside class="sidebar">
    <h2>A RECENT SUCCESS</h2>
    <div class="title-rule"></div>
    <div class="news-item">
      <p class="intro">Check and/or subscribe to our weekly newsletters for up-todate telecom news. Below are older news items. <span class="date">31 Aug, 2020</span></p>
      <p>The Federal Communications Commission is proceeding with a proposed rule on revisions to its rules implementing the Telephone Robocall Abuse Criminal Enforcement and Deterrence Act (TRACED Act) in a request for comment announced Friday .</p>
    </div>
    <div class="news-item">
      <h3>FCC Grants Safe Harbor For Robo Call Blocking <span class="date">July, 2020</span></h3>
      <p>The Federal Communications Commission (FCC) has now approved “two safe harbors from liability for the unintended or inadvertent blocking of wanted calls,</p>
    </div>
    <div class="sources">
      <a href="#">,”(https://docs.rcx.gov/public/attachments<br>/DOC-204118B2.pdf).</a>
      <a href="#">,”(https://docs.rcx.gov/public/attachments<br>/DOC-204118B2.pdf).</a>
      <a href="#">,”(https://docs.rcx.gov/public/attachments</a>
    </div>
    <a class="view-more" href="#">VIEW MORE</a>
  </aside>

  <div class="ad">
    <div class="ad-visual" role="img" aria-label="Photo of a hand holding a glowing globe with network connections"></div>
    <div class="ad-caption">INNOVATIVE TELECOM<br>ANALYTICS</div>
  </div>

  <footer class="footer">
    <div class="legal">Copyrights@2024.Halvorsen - Quibb.All Rights Reserved</div>
    <div class="code">C52</div>
  </footer>
</body>
</html>
```